Velvet Lantern rebranding my business with a new business card

I have my new logo and now I need a refresher on my business cards. I really want something fun and fresh. I like black background or anything to make the color pop.
Logo
Name: Velvet Lantern
Contact Info as stated below:
Mira Pellow
555-013-4762
Logo
Name: Velvet Lantern
Mira Pellow
555-013-4762
fb.me/VelvetLanternbyMira
Instagram: @VelvetLanternbyMira

Industry/Entity Type

Business

Contact Information for Business Card

double-sided. Logo on one side. Contact info on the other.

Requirements
Must have
• Logo
• Name: Velvet Lantern
• Contact Info as stated below:
• Mira Pellow
• 555-013-4762
• fb.me/VelvetLanternbyMira
• fb.me/VelvetLanternbyMira

```html
<!DOCTYPE html>
<html lang="en">
<head>
<meta charset="utf-8">
<title>Velvet Lantern – Business Card</title>
<link rel="stylesheet" href="https://fonts.googleapis.com/css2?family=Source+Sans+3:wght@400;600&display=swap">
<style>
  :root {
    --canvas: #ecebe8;
    --card-pink: #f7bcc0;
    --card-white: #ffffff;
    --accent-pink: #ef8d9b;
    --ink: #2a2a2a;
    --wave-black: #0d0d0d;
    --wave-beige: #d8cfb2;
    --shadow: 0 6px 18px rgba(0,0,0,0.18);
  }
  * { box-sizing: border-box; margin: 0; padding: 0; }
  html, body {
    width: 1200px; height: 900px; overflow: hidden;
    background: var(--canvas);
    font-family: "Source Sans 3", "Myriad Pro", Arial, sans-serif;
  }
  .sheet {
    width: 1200px; height: 900px;
    display: flex; flex-direction: column; align-items: center; justify-content: center;
    gap: 40px;
  }
  .card {
    position: relative; width: 700px; height: 400px;
    box-shadow: var(--shadow); overflow: hidden;
  }
  .card--back { background: var(--card-pink); display: flex; align-items: center; justify-content: center; }
  .card--front { background: var(--card-white); }

  .brand-mark {
    font-weight: 600; font-size: 40px; letter-spacing: 1px;
    color: var(--ink); white-space: nowrap;
  }
  .card--front .brand-mark {
    position: absolute; left: 48px; top: 120px; font-size: 36px;
  }

  .wave { position: absolute; inset: 0; width: 100%; height: 100%; }
  .wave__beige { fill: var(--wave-beige); }
  .wave__black { fill: var(--wave-black); }

  .holder-name {
    position: absolute; left: 400px; top: 60px;
    font-size: 22px; font-weight: 400; letter-spacing: 0.5px;
    text-transform: uppercase; color: var(--accent-pink);
  }
  .contact-list {
    position: absolute; left: 385px; top: 118px;
    list-style: none; display: flex; flex-direction: column; gap: 9px;
  }
  .contact-list__item {
    display: flex; align-items: center; gap: 10px;
    font-size: 16px; color: var(--ink);
  }
  .contact-list__icon { width: 20px; height: 20px; flex: none; }
  .contact-list__icon circle { fill: var(--accent-pink); }
  .contact-list__icon path { fill: #fff; }
</style>
</head>
<body>
<main class="sheet">
  <section class="card card--back" aria-label="Card back">
    <span class="brand-mark">Velvet Lantern</span>
  </section>

  <section class="card card--front" aria-label="Card front">
    <svg class="wave" viewBox="0 0 700 400" preserveAspectRatio="none" aria-hidden="true">
      <path class="wave__beige" d="M0,328 C180,324 330,272 470,236 C570,210 640,204 700,202 L700,400 L0,400 Z"/>
      <path class="wave__black" d="M0,346 C190,343 340,296 480,258 C580,232 645,224 700,220 L700,400 L0,400 Z"/>
    </svg>

    <span class="brand-mark">Velvet Lantern</span>

    <h1 class="holder-name">Mira Pellow</h1>
    <ul class="contact-list">
      <li class="contact-list__item">
        <svg class="contact-list__icon" viewBox="0 0 20 20" aria-hidden="true">
          <circle cx="10" cy="10" r="10"/>
          <path d="M6.2 5.2l1.8-.4 1 2.4-1.1.9c.6 1.3 1.6 2.3 2.9 2.9l.9-1.1 2.4 1-.4 1.8c-.1.4-.5.7-.9.7C9.3 13.4 6.6 10.7 5.5 6.1c0-.4.3-.8.7-.9z"/>
        </svg>
        <span>555-013-4762</span>
      </li>
      <li class="contact-list__item">
        <svg class="contact-list__icon" viewBox="0 0 20 20" aria-hidden="true">
          <circle cx="10" cy="10" r="10"/>
        </svg>
        <span>fb.me/VelvetLanternbyMira</span>
      </li>
    </ul>
  </section>
</main>
</body>
</html>
```